Shipping Container Sales & Leasing Flyer

We need a flyer that is going to be presented and left behind while prospecting potential customers. The service we are selling is the sale, rental and customization of 20' and 40' shipping containers.

We provide new and used containers to customers for various reasons, mainly storage. We also custom modify containers into storage units, mobile offices, mobile job site storage, command centers, pump houses, garages, living space, the only limit is the customers imagination.

I would like our company logo and phone / email at the bottom but the design should showcase some of the attached images ive provided as examples and have spots where we can list the types of equipment we have for sale and the various types of conversions we can offer.

Please also tie in to the colour scheme of our logo.

Target Market(s)

Moving & Storage, Construction, Contractors, Business to Business, Any business that needs portable storage, Landscapers, Property Maintenance companies.

Industry/Entity Type

Shipping

Font styles to use
Serif
Sans Serif

Requirements
Must have
• Professional feel, clean original design.
Nice to have
• Tie in to our logo colour scheme.
Should not have
• Bulky or crowded look

```html
<!DOCTYPE html>
<html lang="en">
<head>
<meta charset="utf-8">
<title>Containers – Sale, Rental &amp; Customization</title>
<link href="https://fonts.googleapis.com/css2?family=Montserrat:wght@700&family=Noto+Sans:wght@400;700&display=swap" rel="stylesheet">
<style>
  :root {
    --green: #6a9a3c;
    --panel-grey: #6b6d6a;
    --band-grey: #e6e6e6;
    --white: #ffffff;
    --ink-light: #f2f2f2;
    --photo-blue: #5f7fa8;
    --photo-pale: #d8dde2;
    --photo-sand: #b9ad86;
    --photo-steel: #9a9d9c;
  }
  html, body { margin: 0; padding: 0; overflow: hidden; }
  body { width: 849px; height: 1200px; background: var(--white); }
  .flyer {
    position: relative; width: 849px; height: 1200px; overflow: hidden;
    background: var(--white); font-family: "Noto Sans", sans-serif;
  }
  .flyer__shapes { position: absolute; inset: 0; }

  .title-block {
    position: absolute; left: 200px; top: 282px; margin: 0; width: 700px;
    transform: rotate(-24deg); transform-origin: left top;
  }
  .title-block__word {
    display: block; font-family: "Montserrat", sans-serif; font-weight: 700;
    font-size: 86px; line-height: 1; letter-spacing: 0; color: var(--green);
    white-space: nowrap;
  }
  .title-block__tagline {
    display: inline-block; margin-top: 2px; margin-left: 30px; padding: 4px 14px;
    background: var(--green); color: var(--white);
    font-family: "Montserrat", sans-serif; font-weight: 700; font-size: 21px; letter-spacing: 1px;
    white-space: nowrap;
  }

  .services {
    position: absolute; left: 243px; top: 455px; width: 606px; color: var(--ink-light);
  }
  .services__heading {
    margin: 0 0 0 40px; font-weight: 400; font-size: 33px; letter-spacing: .5px; line-height: 1.2;
  }
  .services__rule { height: 3px; background: var(--white); margin: 12px 0 14px; }
  .services__list { list-style: none; margin: 0; padding: 0 22px 0 40px; }
  .services__item {
    position: relative; font-size: 27px; letter-spacing: 1px; line-height: 34px; margin-bottom: 15px;
  }
  .services__item::before {
    content: ""; position: absolute; left: -27px; top: 10px;
    border-left: 10px solid var(--white); border-top: 7px solid transparent; border-bottom: 7px solid transparent;
  }

  .contact {
    position: absolute; left: 300px; top: 945px; width: 310px; margin: 0; padding: 0; list-style: none;
  }
  .contact__row {
    display: flex; justify-content: flex-end; align-items: center; height: 45px;
    font-size: 16px; color: var(--green); white-space: nowrap;
  }
  .contact__badge {
    flex: none; width: 24px; height: 24px; margin-left: 10px; margin-right: -12px; border-radius: 50%;
    background: var(--white); color: var(--green); font-weight: 700; font-size: 15px;
    display: flex; align-items: center; justify-content: center;
  }

  .brand { position: absolute; left: 610px; top: 940px; width: 239px; text-align: center; color: var(--green); }
  .brand__dot { width: 110px; height: 110px; margin: 0 auto 14px; border-radius: 50%; background: var(--green); }
  .brand__name { display: block; font-weight: 700; font-size: 52px; line-height: 1; letter-spacing: 6px; }
  .brand__sub { display: block; font-weight: 700; font-size: 13px; letter-spacing: 5px; margin-top: 4px; }
</style>
</head>
<body>
<main class="flyer">
  <svg class="flyer__shapes" width="849" height="1200" viewBox="0 0 849 1200">
    <defs>
      <linearGradient id="g-yard" x1="0" y1="0" x2="1" y2="1">
        <stop offset="0" stop-color="#7f9cc4"/><stop offset="1" stop-color="#4f6f98"/>
      </linearGradient>
      <linearGradient id="g-blue" x1="0" y1="0" x2="1" y2="1">
        <stop offset="0" stop-color="#3a6cbf"/><stop offset="1" stop-color="#1f4d98"/>
      </linearGradient>
    </defs>
    <polygon points="0,0 849,0 849,40 0,330" fill="url(#g-yard)" role="img" aria-label="Open-sided container with lumber stored inside"/>
    <polygon points="243,420 849,160 849,913 243,822" fill="var(--panel-grey)"/>
    <rect x="565" y="234" width="284" height="211" fill="var(--photo-steel)" role="img" aria-label="Grey 20 foot shipping container"/>
    <polygon points="0,338 213,284 213,479 0,513" fill="var(--photo-pale)" role="img" aria-label="Container interior fitted out as a work space"/>
    <polygon points="0,525 213,487 213,670 0,713" fill="var(--photo-blue)" role="img" aria-label="Container with side opening storing lumber"/>
    <polygon points="0,725 213,680 213,822 0,890" fill="var(--photo-sand)" role="img" aria-label="Container fitted with a roll-up door"/>
    <polygon points="0,900 210,862 849,945 849,1160 0,1160" fill="var(--band-grey)"/>
    <polygon points="0,930 330,905 345,1187 0,1187" fill="url(#g-blue)" role="img" aria-label="Blue 20 foot shipping container"/>
    <line x1="586" y1="925" x2="586" y2="1141" stroke="var(--panel-grey)" stroke-width="2"/>
  </svg>

  <h1 class="title-block">
    <span class="title-block__word">CONTAINERS</span>
    <span class="title-block__tagline">Reasonable Customised Storage on the Go.</span>
  </h1>

  <section class="services">
    <h2 class="services__heading">SALE, RENTAL &amp; CUSTOMIZATION</h2>
    <div class="services__rule"></div>
    <ul class="services__list">
      <li class="services__item">20' and 40' shipping containers.</li>
      <li class="services__item">New and Used Containers.</li>
      <li class="services__item">Custom modify containers into storage units, mobile offices, mobile job site storage, command centers, pump houses, garages, living space, the only limit is the customers imagination.</li>
    </ul>
  </section>

  <ul class="contact">
    <li class="contact__row">Canada<span class="contact__badge">A</span></li>
    <li class="contact__row">800-ternmgmt<span class="contact__badge">P</span></li>
    <li class="contact__row">info@ternmanagement.com<span class="contact__badge">E</span></li>
    <li class="contact__row">www.ternmanagement.com<span class="contact__badge">W</span></li>
  </ul>

  <div class="brand">
    <div class="brand__dot"></div>
    <span class="brand__name">TERN</span>
    <span class="brand__sub">MANAGEMENT</span>
  </div>
</main>
</body>
</html>
```